Business Card Design

We need the business card for our new business based in St. Marys, we manufacture mainly bubble wraps. And we would like the design to use our company logo and also make it easy for people to understand right away we are bubble wrap manufacturer

Industry/Entity Type

Business

Contact Information for Business Card

Cushtane Pty Ltd, 14 Larkin Road Kellhaven NSW 2764, Tel: 02 9471 5826, Fax: 9471 5839, Dara Oyelaran, General Manager, Mobile :0438 217 564, dara.oyelaran@cushtane.com.au, Website: cushtane.com.au

```html
<!DOCTYPE html>
<html lang="en">
<head>
<meta charset="utf-8">
<title>Cushtane Business Card</title>
<link rel="stylesheet" href="https://fonts.googleapis.com/css2?family=Arimo:wght@400;700&display=swap">
<style>
  :root {
    --stage: #e9e7e4;
    --card: #ffffff;
    --card-shade: #eeeeee;
    --ink: #55565a;
    --ink-soft: #7a7b7e;
    --accent: #b8252c;
    --band: #58585b;
    --band-text: #f2f2f2;
    --rule: #c9c9c9;
  }
  * { box-sizing: border-box; margin: 0; padding: 0; }
  html, body { width: 1200px; height: 848px; overflow: hidden; }
  body {
    background: var(--stage);
    font-family: "Arimo", Arial, sans-serif;
    color: var(--ink);
    display: flex;
    flex-direction: column;
    align-items: center;
    justify-content: center;
    gap: 40px;
  }
  .card {
    width: 600px;
    height: 343px;
    border-radius: 18px;
    background: var(--card);
    box-shadow: 0 6px 18px rgba(0,0,0,0.12);
    position: relative;
    overflow: hidden;
  }
  .wordmark { display: inline-flex; flex-direction: column; align-items: flex-end; }
  .wordmark-row { display: flex; align-items: center; gap: 10px; }
  .wordmark-square { width: 18px; height: 18px; background: var(--accent); }
  .wordmark-name {
    font-weight: 700;
    color: var(--ink);
    letter-spacing: 1px;
    line-height: 1;
  }
  .wordmark-tagline {
    font-weight: 400;
    color: var(--ink-soft);
    text-transform: uppercase;
    margin-top: 8px;
  }
  .card-front { display: flex; align-items: center; justify-content: center; }
  .card-front .wordmark-name { font-size: 56px; }
  .card-front .wordmark-square { width: 34px; height: 34px; }
  .card-front .wordmark-tagline { font-size: 12px; letter-spacing: 4.2px; }
  .card-back {
    background: linear-gradient(110deg, var(--card-shade) 0%, var(--card) 60%);
  }
  .back-logo {
    position: absolute;
    left: 0; top: 0;
    width: 290px; height: 293px;
    display: flex; align-items: center; justify-content: center;
  }
  .back-logo .wordmark-name { font-size: 36px; }
  .back-logo .wordmark-square { width: 20px; height: 20px; }
  .back-logo .wordmark-tagline { font-size: 7.5px; letter-spacing: 2.6px; margin-top: 5px; }
  .divider {
    position: absolute;
    left: 290px; top: 0;
    width: 1px; height: 293px;
    background: var(--rule);
  }
  .contact {
    position: absolute;
    left: 330px; top: 38px;
    right: 20px;
  }
  .contact-name { font-size: 27px; font-weight: 400; color: var(--ink); line-height: 1; }
  .contact-role { font-size: 11px; color: var(--ink-soft); margin-top: 4px; }
  .contact-list { list-style: none; margin-top: 30px; }
  .contact-list li {
    display: flex; align-items: center; gap: 12px;
    font-size: 14px; color: var(--ink); line-height: 1; height: 21px;
    white-space: nowrap;
  }
  .contact-list svg { width: 12px; height: 12px; flex: none; fill: none; stroke: var(--ink); stroke-width: 1.4; }
  .contact-list svg .solid { fill: var(--ink); stroke: none; }
  .address-band {
    position: absolute;
    left: 0; right: 0; bottom: 0;
    height: 50px;
    background: var(--band);
    color: var(--band-text);
    font-size: 16px;
    display: flex; align-items: center; justify-content: center;
  }
</style>
</head>
<body>

  <section class="card card-front" aria-label="Card front">
    <div class="wordmark">
      <div class="wordmark-row">
        <span class="wordmark-square"></span>
        <span class="wordmark-name">CUSHTANE</span>
      </div>
      <span class="wordmark-tagline">Protective Packaging Solutions</span>
    </div>
  </section>

  <section class="card card-back" aria-label="Card back">
    <div class="back-logo">
      <div class="wordmark">
        <div class="wordmark-row">
          <span class="wordmark-square"></span>
          <span class="wordmark-name">CUSHTANE</span>
        </div>
        <span class="wordmark-tagline">Protective Packaging Solutions</span>
      </div>
    </div>
    <div class="divider"></div>
    <div class="contact">
      <p class="contact-name">Dara Oyelaran</p>
      <p class="contact-role">General Manager</p>
      <ul class="contact-list">
        <li>
          <svg viewBox="0 0 12 12" aria-hidden="true"><path class="solid" d="M2 1h2.5l1 3-1.5 1a6 6 0 0 0 3 3l1-1.5 3 1V10a1 1 0 0 1-1 1A10 10 0 0 1 1 2a1 1 0 0 1 1-1z"/></svg>
          <span>02 9471 5826</span>
        </li>
        <li>
          <svg viewBox="0 0 12 12" aria-hidden="true"><rect x="3" y="1" width="6" height="10" rx="1"/><line x1="5.5" y1="9" x2="6.5" y2="9"/></svg>
          <span>0438 217 564</span>
        </li>
        <li>
          <svg viewBox="0 0 12 12" aria-hidden="true"><rect x="3" y="1" width="6" height="3"/><rect x="1" y="4" width="10" height="5" rx="1"/><rect x="3" y="7" width="6" height="4"/></svg>
          <span>9471 5839</span>
        </li>
        <li>
          <svg viewBox="0 0 12 12" aria-hidden="true"><rect x="1" y="1.5" width="10" height="7" rx="0.5"/><line x1="6" y1="8.5" x2="6" y2="10.5"/><line x1="3.5" y1="10.5" x2="8.5" y2="10.5"/></svg>
          <span>cushtane.com.au</span>
        </li>
        <li>
          <svg viewBox="0 0 12 12" aria-hidden="true"><path class="solid" d="M1 3h10v6H1z"/><path d="M1 3l5 3.5L11 3" stroke="#fff"/></svg>
          <span>dara.oyelaran@cushtane.com.au</span>
        </li>
      </ul>
    </div>
    <div class="address-band">Cushtane Pty Ltd, 14 Larkin Road Kellhaven NSW 2764</div>
  </section>

</body>
</html>
```